Lumira Skincare packaging designs

We are need to create packaging for our skincare brand. We need two designs. One for round jars which is for creams/capsules and the second will be for bottles/serums Some products will be larger in size so please ensure the packaging design will work and there isn't a lot white/empty space

Below are the names of some of our products.
Screw-On Top Jar (25 pads- 4 inches wide) - Velvet Swipes I Skin Brightening Pads
Pump Bottle (2 oz) - AquaLoft I Hyaluronic Acid + Vitamin Serum
Pump Bottle (6oz) - The Petal Wash I Conditioning Face Cleanser
Dropper bottle (1 oz) - Morning Mist I Hydrating Moisturizer
Cream jar (1.5 oz) - Morning Mist I Hydrating Moisturizer
Capsules Jar (25 capsules in a jar)- Plume Drop I Moisture + Hydrating Capsules
Capsules Jar (25 capsules in a jar) - Pure Pulse I Impurity Capsules

We will also need help with the packing design in terms of layout of the logo, item name, desc, and ingredients on each product.

Target Market(s)

women

Industry/Entity Type

skincare, beauty

Font styles to use
Sans Serif

Colors
E54698
E96AAD
F1A4CE
F9D9EA
FCEFF6

Requirements
Must have
• Pantone color is 2052 CP HEX #DAAFCA (218 , 175 , 202)

```html
<!DOCTYPE html>
<html lang="en">
<head>
<meta charset="UTF-8">
<title>Morning Mist Hydration Serum Label</title>
<link rel="stylesheet" href="https://fonts.googleapis.com/css2?family=Questrial&display=swap">
<style>
  :root {
    --page-bg: #ffffff;
    --pink-light: #f9c6dc;
    --pink-mid: #f4a6c4;
    --pink-line: #ef8fb8;
    --frame-white: rgba(255, 255, 255, 0.55);
    --silver-light: #ffffff;
    --silver-mid: #b9b9b9;
    --ink-dark: #2b2b2b;
    --ink-grey: #9a9a9a;
    --band-white: #ffffff;
  }
  * { margin: 0; padding: 0; box-sizing: border-box; }
  html, body {
    width: 1200px;
    height: 1000px;
    overflow: hidden;
    background: var(--page-bg);
    font-family: "Questrial", sans-serif;
  }
  .canvas {
    position: relative;
    width: 1200px;
    height: 1000px;
  }
  .label {
    position: absolute;
    left: 310px;
    top: 80px;
    width: 580px;
    height: 840px;
    background: linear-gradient(90deg, var(--pink-light) 0%, var(--pink-mid) 50%, var(--pink-light) 100%);
    overflow: hidden;
  }
  .label-frames {
    position: absolute;
    left: 0;
    top: 0;
    width: 580px;
    height: 540px;
  }
  .brand-name {
    position: absolute;
    left: 0;
    top: 238px;
    width: 580px;
    text-align: center;
    color: #ffffff;
    font-size: 30px;
    letter-spacing: 2px;
  }
  .product-band {
    position: absolute;
    left: 33px;
    top: 521px;
    width: 514px;
    height: 114px;
    background: linear-gradient(90deg, var(--silver-light) 0%, var(--silver-mid) 45%, var(--silver-mid) 60%, var(--silver-light) 100%);
    display: flex;
    align-items: center;
    justify-content: center;
  }
  .product-name {
    font-size: 70px;
    color: var(--ink-dark);
    line-height: 1;
  }
  .descriptor-band {
    position: absolute;
    left: 33px;
    top: 635px;
    width: 514px;
    height: 89px;
    background: var(--band-white);
    display: flex;
    align-items: center;
    justify-content: center;
  }
  .product-descriptor {
    font-size: 40px;
    color: var(--ink-grey);
  }
  .product-volume {
    position: absolute;
    left: 0;
    top: 766px;
    width: 580px;
    text-align: center;
    font-size: 32px;
    color: var(--ink-dark);
  }
</style>
</head>
<body>
  <main class="canvas">
    <section class="label">
      <svg class="label-frames" viewBox="0 0 580 540" aria-hidden="true">
        <polygon points="290,4 545,258 290,512 35,258" fill="none" stroke="var(--pink-line)" stroke-width="2"/>
        <polygon points="262,64 486,238 318,457 94,284" fill="none" stroke="var(--frame-white)" stroke-width="2"/>
      </svg>
      <p class="brand-name">Lumira Skincare</p>
      <div class="product-band">
        <h1 class="product-name">Morning Mist</h1>
      </div>
      <div class="descriptor-band">
        <p class="product-descriptor">Hydration Serum</p>
      </div>
      <p class="product-volume">1 fl. oz (29.5ml)</p>
    </section>
  </main>
</body>
</html>
```